Nitrogen generation business website

Project Overview:
This project aims to create a sleek, user-friendly, and responsive WordPress template for Flo7K3, a provider of Nitrogen generation solutions. The site will serve as a primary touchpoint for customers and businesses looking to enquire about or purchase Flo7K3 products and services. The website should clearly communicate the benefits of working with Flo7K3 as a distributor, focusing on ease of access, expert consultation, and fast, reliable service.
Target Audience:
• Industrial companies seeking Nitrogen solutions.
• Engineers, facility managers, and purchasing teams in need of high-quality Nitrogen systems.
• Partners or businesses seeking to collaborate or purchase through a distributor.
Key Objectives:
1. Establish Flo7K3’s Brand Identity: Use the bold, energetic logo and branding of Flo7K3 (as seen in the uploaded logo) throughout the design. Ensure the brand’s personality shines, with a focus on modernity, reliability, and innovation.
2. Showcase Products and Solutions: Display detailed product categories and descriptions, emphasising the solutions Flo7K3 offers.
3. Lead Generation: Incorporate contact forms, quote requests, and easy-to-find CTAs to convert visitors into leads.
4. User-Centric Design: The design must be intuitive and user-friendly, providing a smooth experience across desktop and mobile devices.
Design Requirements:
1. Home Page:
• Hero Banner: A dynamic, visually engaging hero banner featuring air and gas purification systems, paired with strong CTAs like “Request a Quote” or “Contact Us for Solutions.” The banner should align with the vibrant red and yellow tones in the Flo7K3 logo.
• Key Product Categories: Introduce the main product categories with icons or images linked to individual product pages.
• Flo7K3 Expertise Section: A section emphasising the company’s role as a trusted distributor, backed by experience and a strong partnership network.
• Why Choose Flo7K3: Highlight 3-4 major benefits, such as “Quick Delivery,” “Expert Consultation,” and “Innovative Technology.”
• Client Testimonials/Partners: Space for customer feedback, testimonials, or logos of partner companies to build trust.
• Newsletter or Enquiry Form: Place a compact form for capturing visitor details for quotes, enquiries, or subscriptions.
2. Product Pages:
• Category Pages: Create well-structured product category pages (e.g., Air Filtration Systems, Nitrogen Generators) similar to industry-standard designs. Each category page should feature professional imagery, short product descriptions, and links to detail pages.
• Product Detail Pages: Each product page will contain:
• High-quality images of the product.
• Detailed specifications, technical descriptions, and features.
• Options to download datasheets or brochures (PDF format).
• Clear CTAs to request a quote or contact sales.
• Product Comparison Tool (Optional): Allow users to compare multiple products, emphasising key features and specifications.
3. About Flo7K3 Page:
• Provide an overview of Flo7K3’s history, mission, and the value it provides as a leading distributor.
• Highlight industry expertise, the partnership network, and any accolades or certifications.
• Mention any regional advantages or special services (e.g., fast delivery times, on-site consultation).
4. Contact Us Page:
• Clean and Simple Form: Include fields for general inquiries or specific product requests.
• Contact Information: Display the company’s, email address info@flo7k3.co.uk.
5. Additional Functionalities:
• Responsive Design: Ensure the design is fully responsive, optimised for mobile, tablet, and desktop viewing.
• SEO Optimisation: Include best practices for search engine optimization (SEO), including clean URLs, meta tags, and image alt text.
• Fast Loading Speed: Optimise images, scripts, and code for fast loading times to improve user experience.
• Social Media Integration: Provide links to social media profiles (if applicable) and potentially include a feed for recent updates.
• Optional Blog: Create a blog space for sharing industry news, product updates, or educational content to engage with visitors and improve SEO.
Style Guide:
1. Color Palette:
• Use colors consistent with the Flo7K3 logo: Red (#FF0000) and Yellow (#FFD700) as primary colors. Incorporate neutral colors (such as white, gray, or black) for balance and readability.
• Accent colors may be introduced for subtle highlights, but the focus should be on the bold, energetic color scheme of Flo7K3.
2. Typography:
• Primary Font for Headings: A bold, modern sans-serif font that complements the strong branding of Flo7K3.
• Secondary Font for Body Text: Clean, easy-to-read sans-serif or serif font for optimal readability across devices.
• Typography Emphasis: Use large, bold typography for headlines to match the boldness of the logo and brand identity.
3. Imagery:
• Use high-quality industrial and technical imagery that reflects the air and gas purification products Flo7K3 distributes.
• Incorporate imagery showing products in action, e.g., in industrial settings or installations.
• Avoid clutter; ensure images are used to enhance user understanding, not overwhelm.
4. Icons:
• Utilise modern, flat-style icons that align with the clean and professional image of Flo7K3. Icons could represent services such as “Fast Delivery,” “Expert Support,” and “High-Quality Products.”
Functionality Requirements:
1. Content Management System (CMS): Build the site using WordPress for easy content management, allowing Flo7K3 staff to update content, product information, and blog posts.
2. Quote Request Integration: Ensure the site has a functional and easy-to-access “Request a Quote” form that appears on every product and service page.
3. Customer Support Section: Optionally include a section for FAQs, product guides, or a knowledge base to support customers and prospects.
4. Security: Implement SSL encryption and ensure that other security best practices (e.g., spam prevention for forms) are followed.
5. Multilingual Support (Optional): Provide the option to support multiple languages, depending on the regional scope of Flo7K3’s distribution services.
Deliverables:
• WordPress template with a homepage, product pages, about section, and contact page.
• SEO-friendly and responsive design.
• Clear CTAs for lead generation (e.g., “Request a Quote”).
• User-friendly interface for both desktop and mobile devices.
Inspiration/Competitors:
• Competitor Analysis: Research similar distributors in the air and gas purification industry for design inspiration.
• Brand Consistency: Ensure Flo7K3’s bold branding is prominent and differentiates it from competitors.
Target Market(s)
Food & Beverage manufacturers, Laser Cutting, Electronics manufacturers, General Industrial Manufacturers

```html
<!DOCTYPE html>
<html lang="en">
<head>
<meta charset="utf-8">
<title>Flo7K3 – Nitrogen Generators</title>
<link rel="stylesheet" href="https://fonts.googleapis.com/css2?family=Work+Sans:wght@400;500;600;700&display=swap">
<style>
:root{
  --board:#393c38;
  --paper:#f6f7f9;
  --red:#ff1a00;
  --yellow:#ffb400;
  --ink:#111;
  --muted:#444;
  --line:#f2585a;
  --card:#dde3e3;
}
*{box-sizing:border-box;margin:0;padding:0}
html,body{width:1200px;height:1200px;overflow:hidden;background:var(--board);font-family:"Work Sans",sans-serif;color:var(--ink)}
.page{position:absolute;background:var(--paper);overflow:hidden}
.page *{position:absolute}
.page br,.page .crumb span,.page .flow *{position:static}
.brand{font-weight:700;color:var(--red);letter-spacing:-.02em;white-space:nowrap}
.nav{display:flex;gap:6px;white-space:nowrap;font-weight:500}
.nav span{position:static}
.nav .on{color:var(--red);font-weight:700}
.icon{stroke:var(--ink);fill:none}
.red{color:var(--red)}
.photo{background:linear-gradient(160deg,#d9dcdf,#9aa0a6);border-radius:6px}

/* listing page */
.listing{left:170px;top:143px;width:458px;height:845px}
.listing .brand{left:48px;top:15px;font-size:17px}
.listing .nav{left:183px;top:21px;font-size:3.6px}
.hero{left:0;top:43px;width:458px;height:187px;background:var(--red);border-bottom-left-radius:52px;overflow:hidden}
.hero .accent{left:299px;top:54px;width:200px;height:180px;background:var(--yellow);border-top-left-radius:42px}
.hero .machine{left:278px;top:7px;width:136px;height:167px}
.hero h1{left:45px;top:22px;font-size:23px;font-weight:500;line-height:27px;color:#fff}
.hero p{left:48px;top:85px;width:205px;font-size:7.4px;line-height:9px;color:#fff}
.dots{left:48px;top:156px;display:flex;gap:4px}
.dots i{position:static;width:5px;height:5px;border-radius:50%;border:1px solid var(--yellow)}
.dots i:first-child{background:var(--yellow)}
.crumb{font-size:7.5px;white-space:nowrap}
.listing .crumb{left:48px;top:253px}
.intro-title{left:48px;top:281px;width:280px;font-size:15.5px;line-height:18px;font-weight:600}
.intro-copy{left:48px;top:354px;width:360px;font-size:7.3px;line-height:9.2px;color:var(--muted)}
.intro-copy p{margin-bottom:9px}
.cat{width:179px;height:96px;border-radius:8px;overflow:hidden}
.cat.r{background:var(--red)}
.cat.y{background:var(--yellow)}
.cat h3{left:13px;top:16px;width:90px;font-size:11px;line-height:13.5px;font-weight:500}
.cat.r h3{color:var(--yellow)}
.cat .arch{left:100px;top:36px;width:64px;height:80px;border-radius:32px 32px 0 0}
.cat.r .arch{background:var(--yellow)}
.cat.y .arch{background:var(--red)}
.cat .shot{left:112px;top:10px;width:58px;height:86px;border-radius:4px;background:linear-gradient(160deg,#eceeef,#8d9296)}
.cat .btn{left:12px;top:68px;padding:3px 7px;border-radius:3px;font-size:5.5px;font-weight:500}
.cat.r .btn{background:var(--yellow);color:var(--red)}
.cat.y .btn{background:var(--red);color:var(--yellow)}

/* footer */
.foot{left:0;background:var(--yellow);border-top-left-radius:52px}
.foot h4{font-weight:600}
.foot .small{color:#6a3b00}
.social{display:flex}
.social i{position:static;border-radius:50%;background:var(--red)}
.listing .foot{top:672px;width:458px;height:173px}
.listing .foot .brand{left:48px;top:44px;font-size:15px;color:#fff}
.listing .foot h4{top:50px;font-size:7.5px}
.listing .foot .small{font-size:4.3px;line-height:5.6px}
.listing .social{gap:10px;top:102px;left:327px}
.listing .social i{width:13px;height:13px}

/* detail page */
.detail{left:682px;top:51px;width:332px;height:1112px}
.detail .brand{left:35px;top:10px;font-size:12px}
.detail .nav{left:132px;top:16px;font-size:2.6px;gap:4px}
.detail .crumb{left:35px;top:37px;font-size:5.2px}
.hero-shot{left:35px;top:54px;width:110px;height:121px;background:var(--yellow);border-radius:6px}
.hero-shot .photo{left:28px;top:16px;width:54px;height:88px}
.detail h1{left:162px;top:54px;width:140px;font-size:10.5px;line-height:13px;font-weight:600}
.lede{left:162px;top:89px;width:132px;font-size:5.4px;line-height:7.2px;color:var(--muted)}
.cta{left:162px;top:157px;width:63px;height:18px;background:var(--red);color:#fff;border-radius:3px;font-size:5px;font-weight:600;display:flex;align-items:center;justify-content:center}
.detail h2{left:35px;font-size:10px;font-weight:600}
.rows{left:37px;width:260px}
.row{position:relative!important;display:flex;justify-content:space-between;align-items:center;border-bottom:.8px solid var(--line);font-size:5.6px;padding:0 5px}
.row b{position:static;font-weight:600}
.row span{position:static}
.acc{top:232px;border-top:.8px solid var(--line)}
.acc .row{height:19.8px}
.acc .open{height:41px;display:block;padding-top:5px}
.acc .open p{position:static;margin-top:6px;font-size:5.2px;line-height:6.8px;color:var(--muted);font-weight:400}
.specs{top:381px}
.specs .row{height:20.7px}
.check{left:43px;display:flex;align-items:center;gap:8px;font-size:5.6px;font-weight:600;white-space:nowrap}
.check i{position:static;width:9px;height:9px;border:1.3px solid var(--red);border-radius:2.5px}
.check i.on{background:radial-gradient(var(--red) 45%,transparent 50%)}
.compare{left:35px;top:612px;width:262px;border-collapse:collapse;font-size:5.4px}
.compare *{position:static}
.compare th{background:var(--yellow);text-align:left;font-weight:600;height:20px;padding:0 3px;line-height:6px}
.compare th:first-child{border-radius:5px 0 0 5px}
.compare th:last-child{border-radius:0 5px 5px 0}
.compare td{border-bottom:.8px solid var(--line);height:17px;padding:0 3px;line-height:6.5px;color:var(--ink)}
.compare tr.tall td{height:25px}
.compare td:first-child{width:88px}
.compare td:nth-child(2){width:99px}
.dl{top:884px}
.dl .row{height:16px}
.dl .open{height:54px;display:block;padding-top:4px}
.guide{position:relative!important;margin-top:6px;width:70px;height:34px;background:var(--card);border-radius:3px;padding:4px 6px;font-size:3.4px;line-height:4.4px}
.guide *{position:static;display:block}
.detail .foot{top:988px;width:332px;height:124px;border-top-left-radius:36px}
.detail .foot .brand{left:35px;top:34px;font-size:11px;color:#fff}
.detail .foot h4{top:37px;font-size:5.2px}
.detail .foot .small{font-size:3px;line-height:3.9px}
.detail .social{gap:7px;top:82px;left:235px}
.detail .social i{width:9px;height:9px}
</style>
</head>
<body>

<!-- Product listing page -->
<section class="page listing">
  <div class="brand">Flo7K3</div>
  <nav class="nav"><span>HOME</span><span class="on">PRODUCT</span><span>ABOUT US</span><span>SERVICES</span><span>BLOG</span><span>CONTACT US</span></nav>
  <svg style="left:372px;top:20px" width="9" height="9" viewBox="0 0 10 10" class="icon" stroke-width="1"><circle cx="5" cy="3.2" r="2.2"/><path d="M1 9.5c0-2.4 1.8-3.8 4-3.8s4 1.4 4 3.8z"/></svg>
  <svg style="left:390px;top:20px" width="9" height="9" viewBox="0 0 10 10" class="icon" stroke-width="1"><rect x="1" y="2.5" width="8" height="7" rx="1"/><path d="M3.5 2.5V1.5h3v1"/></svg>
  <div style="left:406px;top:22px;font-size:3px;color:#888">GBP</div>

  <div class="hero">
    <div class="accent"></div>
    <div class="machine photo" role="img" aria-label="Twin tower PSA nitrogen generator skid"></div>
    <h1>Nitrogen<br>Generators</h1>
    <p>Discover our range of PSA and Membrane Nitrogen Generators designed for high efficiency and reliable on-site nitrogen production.</p>
    <div class="dots"><i></i><i></i><i></i></div>
  </div>

  <div class="crumb">Home &gt; <span class="red">Product</span></div>
  <h2 class="intro-title">Discover Cutting-Edge Nitrogen Generation Solutions Tailored for Your Industry</h2>
  <div class="intro-copy flow">
    <p>Flo7K3 offers a comprehensive range of nitrogen generation systems, designed to meet the diverse needs of industries worldwide. From advanced PSA and membrane nitrogen generators to pre-treatment solutions and monitoring sensors, we provide reliable and cost-effective products that optimize your operations. Our systems ensure high performance, energy efficiency, and ease of use, making on-site nitrogen production more accessible than ever.</p>
    <p>Explore our product categories below to find the perfect solution for your business, and request a quote or expert consultation to get started today.</p>
  </div>

  <article class="cat r" style="left:48px;top:451px">
    <div class="arch"></div>
    <div class="shot" role="img" aria-label="PSA nitrogen generator units"></div>
    <h3>PSA Nitrogen Generator</h3>
    <div class="btn">View Details</div>
  </article>
  <article class="cat y" style="left:233px;top:451px">
    <div class="arch"></div>
    <div class="shot" role="img" aria-label="Membrane nitrogen generator with filters"></div>
    <h3>Membrane Nitrogen Generator</h3>
    <div class="btn">View Details</div>
  </article>
  <article class="cat y" style="left:48px;top:556px">
    <div class="arch"></div>
    <div class="shot" role="img" aria-label="Compressed air pre-treatment filter housing"></div>
    <h3 style="color:var(--ink);top:18px">Pre-Treatment</h3>
    <div class="btn">View Details</div>
  </article>
  <article class="cat r" style="left:233px;top:556px">
    <div class="arch"></div>
    <div class="shot" role="img" aria-label="Oxygen analyser sensor unit"></div>
    <h3 style="top:16px">Sensor</h3>
    <div class="btn">View Details</div>
  </article>

  <footer class="foot">
    <div class="brand">Flo7K3</div>
    <p class="small" style="left:48px;top:74px;width:62px">You minim mollit non deserunt ullamco est sit aliqua dolor do amet sint. Velit officia consequat duis</p>
    <h4 style="left:153px">Get In Touch</h4>
    <svg style="left:153px;top:74px" width="7" height="8" viewBox="0 0 10 12" fill="none" stroke="#ff1a00" stroke-width="1.3"><path d="M5 11s4-4 4-6.5a4 4 0 0 0-8 0C1 7 5 11 5 11z"/><circle cx="5" cy="4.5" r="1.4"/></svg>
    <p class="small" style="left:171px;top:75px;width:52px">2180 Harbour Rd. Leeds, West Yorkshire 40211</p>
    <svg style="left:153px;top:101px" width="8" height="7" viewBox="0 0 10 8" fill="none" stroke="#ff1a00" stroke-width="1.1"><rect x=".6" y=".6" width="8.8" height="6.8" rx="1.5"/><path d="M1.5 2l3.5 2.5L8.5 2"/></svg>
    <p class="small" style="left:171px;top:102px">info@flo7k3.co.uk</p>
    <svg style="left:153px;top:122px" width="8" height="8" viewBox="0 0 10 10" fill="none" stroke="#ff1a00" stroke-width="1.1"><rect x="3" y=".6" width="6.4" height="5" rx="1"/><rect x=".6" y="3.5" width="6.4" height="5" rx="1"/></svg>
    <p class="small" style="left:171px;top:124px">(207) 555-0148<br>(702) 555-0173</p>
    <h4 style="left:245px">Explore Link</h4>
    <p class="small" style="left:246px;top:75px;line-height:14.8px">About Us<br>Career<br>FAQ<br>Blog<br>Product</p>
    <h4 style="left:327px">Office Time</h4>
    <p class="small" style="left:327px;top:75px;line-height:7.8px">Mon-Sat: 10:00AM - 4.00PM<br>Sunday: 10:00AM - 4.00PM<br>Friday: Close</p>
    <div class="social"><i></i><i></i><i></i></div>
  </footer>
</section>

<!-- Product detail page -->
<section class="page detail">
  <div class="brand">Flo7K3</div>
  <nav class="nav"><span>HOME</span><span class="on">PRODUCT</span><span>ABOUT US</span><span>SERVICES</span><span>BLOG</span><span>CONTACT US</span></nav>
  <svg style="left:267px;top:14px" width="6" height="6" viewBox="0 0 10 10" class="icon" stroke-width="1.2"><circle cx="5" cy="3.2" r="2.2"/><path d="M1 9.5c0-2.4 1.8-3.8 4-3.8s4 1.4 4 3.8z"/></svg>
  <svg style="left:280px;top:14px" width="6" height="6" viewBox="0 0 10 10" class="icon" stroke-width="1.2"><rect x="1" y="2.5" width="8" height="7" rx="1"/><path d="M3.5 2.5V1.5h3v1"/></svg>
  <div style="left:292px;top:16px;font-size:2px;color:#888">GBP</div>

  <div class="crumb">Home &gt; Product &gt; PSA Nitrogen Generator &gt; <span class="red">Low Capacity Modular N2 Generator</span></div>
  <div class="hero-shot"><div class="photo" role="img" aria-label="Low capacity modular nitrogen generator cabinet"></div></div>
  <h1>Low Capacity Nitrogen Generators</h1>
  <p class="lede">Flo7K3's Low Capacity Modular N2 Generator is the perfect solution for businesses looking to produce nitrogen on-site in a cost-effective and efficient manner. Designed for small to medium-scale operations, this modular system ensures consistent nitrogen production with minimal energy consumption, reducing your reliance</p>
  <div class="cta">Request Price</div>

  <h2 style="top:196px">Key Features:</h2>
  <div class="rows acc">
    <div class="row open"><b>Energy Efficient</b><span style="float:right">⌃</span><p>The generator uses advanced PSA (Pressure Swing Adsorption) technology to produce nitrogen with low energy consumption, helping you reduce operational costs.</p></div>
    <div class="row"><b>Compact Design</b><span>⌄</span></div>
    <div class="row"><b>High Nitrogen Purity</b><span>⌄</span></div>
    <div class="row"><b>Easy Maintenance</b><span>⌄</span></div>
    <div class="row"><b>Scalable</b><span>⌄</span></div>
  </div>

  <h2 style="top:365px">Technical Specifications</h2>
  <div class="rows specs">
    <div class="row"><b>Capacity</b><span>10-50 Nm³/h</span></div>
    <div class="row"><b>Nitrogen Purity</b><span>95% - 99.5%</span></div>
    <div class="row"><b>Power Consumption</b><span>2.5 kWh</span></div>
    <div class="row"><b>Dimensions (P x L x T)</b><span>1200 x 800 x 1600 mm</span></div>
    <div class="row"><b>Weight</b><span>300 kg</span></div>
    <div class="row"><b>Operating Pressure</b><span>5-8 bar</span></div>
    <div class="row"><b>Noise Level</b><span>≤ 75 dB(A)</span></div>
  </div>

  <h2 style="top:543px">Product Comparison</h2>
  <div class="check" style="top:567px"><i></i>Ultra High Purity N2 Generator</div>
  <div class="check" style="top:588px"><i class="on"></i>High Capacity Twin Tower N2 Generator</div>

  <table class="compare">
    <tr><th>Feature</th><th>Low Capacity Modular<br>N2 Generator</th><th>High Capacity Twin<br>Tower N2 Generator</th></tr>
    <tr><td>Capacity</td><td>10-50 Nm³/h</td><td>100-500 Nm³/h</td></tr>
    <tr><td>Nitrogen Purity</td><td>95% - 99.5%</td><td>95% - 99.5%</td></tr>
    <tr><td>Technology</td><td>PSA</td><td>PSA</td></tr>
    <tr><td>Energy Consumption</td><td>2.5 kWh</td><td>8.0 kWh</td></tr>
    <tr><td>Dimensions (P x L x T)</td><td>1200 x 800 x 1600 mm</td><td>2500 x 1500 x 2000 mm</td></tr>
    <tr><td>Weight</td><td>300 kg</td><td>800 kg</td></tr>
    <tr><td>Operating Pressure</td><td>5-8 bar</td><td>5-10 bar</td></tr>
    <tr><td>Noise Level</td><td>≤ 75 dB(A)</td><td>≤ 85 dB(A)</td></tr>
    <tr class="tall"><td>Maintenance<br>Requirements</td><td>Low</td><td>High</td></tr>
    <tr><td>Suitable Applications</td><td>Small/Mediumscale industries</td><td>Large-scale industrial</td></tr>
    <tr class="tall"><td>Scalability</td><td>High (Modular)</td><td>High (Supports large<br>capacities)</td></tr>
  </table>

  <h2 style="top:866px">Download</h2>
  <div class="rows dl">
    <div class="row"><b>Download Product Datasheet (PDF)</b><span>⌄</span></div>
    <div class="row open"><b>Download Installation Manual (PDF)</b><span style="float:right">⌃</span>
      <div class="guide"><span>User Guide :</span><b style="margin-top:2px">Low Capacity Modular N2 Generator</b><b style="margin-top:4px">Download</b></div>
    </div>
  </div>

  <footer class="foot">
    <div class="brand">Flo7K3</div>
    <p class="small" style="left:35px;top:56px;width:44px">You minim mollit non deserunt ullamco est sit aliqua dolor do amet sint. Velit officia consequat duis</p>
    <h4 style="left:110px">Get In Touch</h4>
    <svg style="left:110px;top:55px" width="5" height="6" viewBox="0 0 10 12" fill="none" stroke="#ff1a00" stroke-width="1.4"><path d="M5 11s4-4 4-6.5a4 4 0 0 0-8 0C1 7 5 11 5 11z"/><circle cx="5" cy="4.5" r="1.4"/></svg>
    <p class="small" style="left:123px;top:56px;width:38px">2180 Harbour Rd. Leeds, West Yorkshire 40211</p>
    <svg style="left:110px;top:74px" width="6" height="5" viewBox="0 0 10 8" fill="none" stroke="#ff1a00" stroke-width="1.2"><rect x=".6" y=".6" width="8.8" height="6.8" rx="1.5"/><path d="M1.5 2l3.5 2.5L8.5 2"/></svg>
    <p class="small" style="left:123px;top:75px">info@flo7k3.co.uk</p>
    <svg style="left:110px;top:90px" width="6" height="6" viewBox="0 0 10 10" fill="none" stroke="#ff1a00" stroke-width="1.2"><rect x="3" y=".6" width="6.4" height="5" rx="1"/><rect x=".6" y="3.5" width="6.4" height="5" rx="1"/></svg>
    <p class="small" style="left:123px;top:91px">(207) 555-0148<br>(702) 555-0173</p>
    <h4 style="left:176px">Explore Link</h4>
    <p class="small" style="left:177px;top:56px;line-height:10.5px">About Us<br>Career<br>FAQ<br>Blog<br>Product</p>
    <h4 style="left:235px">Office Time</h4>
    <p class="small" style="left:235px;top:56px;line-height:5.5px">Mon-Sat: 10:00AM - 4.00PM<br>Sunday: 10:00AM - 4.00PM<br>Friday: Close</p>
    <div class="social"><i></i><i></i><i></i></div>
  </footer>
</section>

</body>
</html>
```